Residential Remodeling Contractor needs updated business card

I need a new design for my business card.
Name of the company is Ridgefell Construction. I need a card that commands presence, strength, integrity. I have been in business for 28 years. I am a Residential Remodeling Contractor that covers all aspects of a residential remodel and build.

```html
<!DOCTYPE html>
<html lang="en">
<head>
<meta charset="utf-8">
<title>Ridgefell Construction – Business Card</title>
<link rel="stylesheet" href="https://fonts.googleapis.com/css2?family=Open+Sans:wght@400;700&display=swap">
<style>
  :root {
    --backdrop: #232323;
    --card-blue: #213f7f;
    --card-blue-deep: #1a3369;
    --ink-white: #ffffff;
  }
  * { margin: 0; padding: 0; box-sizing: border-box; }
  html, body { width: 1200px; height: 780px; overflow: hidden; background: var(--backdrop); }
  body { font-family: "Open Sans", sans-serif; color: var(--ink-white); }
  .canvas { position: relative; width: 1200px; height: 780px; }

  .card {
    position: absolute;
    top: 241px;
    width: 525px;
    height: 298px;
    background: var(--card-blue);
    overflow: hidden;
    box-shadow: 0 10px 30px rgba(0,0,0,.45);
  }
  .card--contact { left: 50px; }
  .card--brand { left: 625px; }

  .contact-panel {
    position: absolute;
    top: 0; right: 0;
    width: 250px; height: 170px;
    background: linear-gradient(200deg, var(--card-blue) 40%, var(--card-blue-deep) 100%);
    clip-path: polygon(22% 0, 100% 0, 100% 100%, 0 100%);
  }
  .person { position: absolute; left: 60px; top: 112px; }
  .person__name { font-weight: 700; font-size: 30px; letter-spacing: .3px; line-height: 1.1; }
  .person__title { font-size: 15px; margin-top: 2px; padding-left: 6px; }

  .contact-list { position: absolute; left: 320px; top: 52px; list-style: none; }
  .contact-list li { display: flex; align-items: center; gap: 8px; font-size: 12.5px; line-height: 1.6; }
  .contact-list svg { width: 12px; height: 12px; flex: none; }

  .address { position: absolute; left: 0; right: 0; bottom: 44px; text-align: center; font-size: 14px; letter-spacing: .2px; }

  .brand { position: absolute; inset: 0; display: flex; align-items: center; justify-content: center; gap: 14px; }
  .brand__mark { width: 22px; height: 22px; border-radius: 50%; background: var(--ink-white); }
  .brand__name { font-weight: 700; font-size: 32px; line-height: 1; letter-spacing: .5px; }
</style>
</head>
<body>
<main class="canvas">
  <section class="card card--contact" aria-label="Business card contact side">
    <div class="contact-panel"></div>
    <div class="person">
      <p class="person__name">Marta Halvorsen</p>
      <p class="person__title">Managing Director</p>
    </div>
    <ul class="contact-list">
      <li>
        <svg viewBox="0 0 12 12" aria-hidden="true"><path d="M2.5 1 L4.5 1 L5 3.5 L3.8 4.5 Q5 7 7.5 8.2 L8.5 7 L11 7.5 L11 9.5 Q10.5 11 9 11 Q1 10 1 3 Q1 1.5 2.5 1 Z" fill="#fff"/></svg>
        (555) 014-2290
      </li>
      <li>
        <svg viewBox="0 0 12 12" aria-hidden="true"><rect x="1" y="2.5" width="10" height="7" fill="none" stroke="#fff" stroke-width="1.2"/><path d="M1 2.5 L6 7 L11 2.5" fill="none" stroke="#fff" stroke-width="1.2"/></svg>
        info@ridgefellbuild.com
      </li>
      <li>
        <svg viewBox="0 0 12 12" aria-hidden="true"><circle cx="6" cy="6" r="5" fill="none" stroke="#fff" stroke-width="1.2"/><ellipse cx="6" cy="6" rx="2.2" ry="5" fill="none" stroke="#fff" stroke-width="1"/><path d="M1 6 H11" stroke="#fff" stroke-width="1"/></svg>
        www.ridgefellbuild.com
      </li>
    </ul>
    <p class="address">418 Cedar Hollow Rd. Suite 120 Millbrook, TX 75010</p>
  </section>

  <section class="card card--brand" aria-label="Business card brand side">
    <div class="brand">
      <span class="brand__mark" aria-hidden="true"></span>
      <span class="brand__name">Ridgefell Construction</span>
    </div>
  </section>
</main>
</body>
</html>
```